Brochure about Gun Trusts

Cover Page: Image of a firearm collection or a lockbox with the title]
Headline: Protect Your Firearms Collection with a Gun Trust
Subheading: Ensure Your Legacy Remains Private and Your Wishes Are Respected
[Page 1: What is a Gun Trust?]
Definition: A legally recognized trust that allows you to collect, own, and transfer firearms, including those restricted by the KRC.
Quote: "A gun trust is a revocable trust created to hold ownership of a firearm..." - BQM
[Page 2: Benefits of a Gun Trust]
Avoid Probate: Keep your firearms out of the public probate process, maintaining your privacy.
Multi-Generational Ownership: Easily transfer ownership to beneficiaries without the need for a court proceeding.
Shared Responsibility: Allow others to legally possess and use the firearms held in the trust.
[Page 3: The Risks of Not Having a Gun Trust]
Inheritance Issues: Firearms may not be transferred as intended, potentially leading to legal complications.
Probate and Public Disclosure: Your firearms collection becomes a public record.
[Page 4: How to Set Up a Gun Trust]
Consult with an Attorney: A firearms trust attorney will create a trust that complies with all federal and state laws.
Assign a Trustee: Choose a trustee to manage the trust if you become incapacitated or pass away.
Transfer Ownership: Assign your firearms to the trust.
[Back Cover: Call to Action]
Headline: Protect Your Firearms Legacy
Contact Information: Address, Phone Number, Email, Website
Offer: Free Consultation to discuss your options

```html
<!DOCTYPE html>
<html lang="en">
<head>
<meta charset="utf-8">
<title>Gun Trust Brochure</title>
<link href="https://fonts.googleapis.com/css2?family=Montserrat:ital,wght@0,300;0,400;0,500;0,600;0,700;0,800;1,400&display=swap" rel="stylesheet">
<style>
  :root{
    --ink:#1f1f1f;
    --yellow:#fdcd2f;
    --white:#ffffff;
    --stage:#efefef;
    --photo-dark-a:#2c2c2c;
    --photo-dark-b:#6b6b6b;
    --photo-light-a:#e8e8e8;
    --photo-light-b:#b9b9b9;
  }
  *{margin:0;padding:0;box-sizing:border-box}
  html,body{width:849px;height:1200px;overflow:hidden;background:var(--stage)}
  body{position:relative;font-family:'Montserrat',sans-serif;color:var(--white)}
  .spread-frame{position:absolute;left:44px;width:760px;height:585px;box-shadow:0 3px 8px rgba(0,0,0,.25)}
  .spread-frame.outside{top:10px}
  .spread-frame.inside{top:605px}
  .spread{position:absolute;left:0;top:0;width:650px;height:500px;background:var(--ink);transform:scale(1.1692);transform-origin:0 0;overflow:hidden}
  .shapes{position:absolute;left:0;top:0;width:650px;height:500px}
  .abs{position:absolute}
  .photo{position:absolute}
  .photo.dark{background:linear-gradient(150deg,var(--photo-dark-a),var(--photo-dark-b) 60%,#4a4a4a)}
  .photo.steel{background:linear-gradient(135deg,#3a3a3a,#8a7d72 55%,#4d4d4d)}
  .photo.light{background:linear-gradient(135deg,var(--photo-light-a),var(--photo-light-b))}
  .photo.wood{background:linear-gradient(160deg,#2a2a2a 0 60%,#6b4a33 60%,#8a5e3e)}
  .pattern-area{position:absolute;left:237px;top:325px;width:210px;height:175px;background:linear-gradient(135deg,var(--yellow) 0%,#8a7330 45%,var(--ink) 100%)}

  /* outside spread */
  .cover-title{left:21px;top:277px;width:175px;font-weight:800;font-size:19.5px;line-height:20.6px;text-transform:uppercase;color:var(--ink)}
  .cover-sub{left:20px;top:385px;width:166px;text-align:right;font-weight:400;font-size:13.5px;line-height:16.6px;letter-spacing:.5px;color:var(--ink)}
  .section-head{font-weight:700;text-transform:uppercase;font-size:16px;line-height:17px;color:var(--white)}
  .risks-head{left:247px;top:60px;width:150px}
  .risk-list{left:252px;top:126px;width:150px;list-style:none;font-size:7.6px;line-height:9.4px}
  .risk-list li{position:relative;padding-left:8px;margin-bottom:12px}
  .risk-list li::before{content:"•";position:absolute;left:0}
  .risk-list b{font-weight:700}
  .cta-offer{left:461px;top:317px;width:180px;font-weight:700;font-size:13px;line-height:14px}
  .cta-contact-head{left:461px;top:362px;font-weight:700;font-size:14.5px}
  .contact-lines{left:461px;top:396px;font-size:8px;line-height:11.6px}

  /* inside spread */
  .define-head{left:13px;top:27px;width:130px;font-weight:700;font-size:20px;line-height:22px;color:var(--yellow)}
  .define-body{left:22px;top:89px;width:140px;font-weight:700;font-size:12px;line-height:14.3px}
  .quote{left:13px;top:438px;width:152px;font-style:italic;font-size:7.4px;line-height:9.6px;color:var(--ink)}
  .benefits-head{left:247px;top:89px;width:145px;font-size:15px;line-height:16px}
  .benefit{position:absolute;left:246px;width:165px}
  .benefit .badge{position:absolute;left:0;top:0;width:18px;height:20px}
  .benefit h3{margin-left:32px;font-weight:500;font-size:10.5px;line-height:10.5px}
  .benefit p{margin-left:32px;margin-top:6px;font-size:7.6px;line-height:10px}
  .setup-head{left:471px;top:300px;width:135px;font-size:14px;line-height:14.5px;text-transform:none}
  .setup-list{left:472px;top:345px;width:145px;list-style:none;font-size:7.6px;line-height:9.6px}
  .setup-list li{position:relative;padding-left:10px;margin-bottom:11px}
  .setup-list li::before{content:"•";position:absolute;left:0}
</style>
</head>
<body>

<!-- Outside spread: cover, risks, call to action -->
<div class="spread-frame outside">
  <section class="spread">
    <svg class="shapes" viewBox="0 0 650 500" aria-hidden="true">
      <polygon fill="var(--yellow)" points="0,267 216,267 216,300 260,300 498,500 95,500 0,418"/>
      <polygon fill="var(--yellow)" points="268,38 394,38 331,0"/>
      <polygon fill="var(--yellow)" points="440,0 610,0 650,40 650,130 575,50 520,38"/>
      <polygon fill="var(--ink)" points="580,0 650,0 650,35"/>
      <polygon fill="var(--yellow)" points="560,145 650,85 650,190"/>
      <line x1="415" y1="0" x2="648" y2="232" stroke="var(--yellow)" stroke-width="1.2"/>
    </svg>

    <div class="photo dark" style="left:0;top:16px;width:186px;height:251px" role="img" aria-label="Photo of a pistol beside an open lockbox with cartridges and cash"></div>
    <h1 class="abs cover-title">Protect Your Firearms Collection with a Gun Trust</h1>
    <p class="abs cover-sub">Ensure Your Legacy Remains Private and Your Wishes Are Respected</p>

    <h2 class="abs section-head risks-head">The Risks of Not Having a Gun Trust</h2>
    <ul class="abs risk-list">
      <li><b>Inheritance Issues:</b> Firearms may not be transferred as intended.</li>
      <li><b>Probate and Public Disclosure:</b> Your firearms collection becomes a public record.</li>
    </ul>
    <div class="photo steel" style="left:246px;top:232px;width:154px;height:110px" role="img" aria-label="Photo of a pistol in an open carry case"></div>
    <div class="photo light" style="left:246px;top:348px;width:154px;height:110px" role="img" aria-label="Photo of hands cleaning a handgun"></div>

    <div class="photo steel" style="left:460px;top:73px;width:187px;height:221px" role="img" aria-label="Photo of a collection of rifles and handguns laid on tiles"></div>
    <p class="abs cta-offer">Free Consultation to discuss your options</p>
    <h2 class="abs cta-contact-head">Contact Us</h2>
    <p class="abs contact-lines">48 Harbor Lane, Millbrook, ST 20418<br>+123-555-0190<br>hello@ironvaultlaw.com<br>www.ironvaultlaw.com</p>
  </section>
</div>

<!-- Inside spread: definition, benefits, setup -->
<div class="spread-frame inside">
  <section class="spread">
    <svg class="shapes" viewBox="0 0 650 500" aria-hidden="true">
      <polygon fill="var(--yellow)" points="250,0 560,0 650,75 650,330 610,300 455,300 455,95 415,63 305,63"/>
      <polygon fill="var(--yellow)" points="0,405 175,405 275,500 0,500"/>
    </svg>
    <div class="pattern-area" role="img" aria-label="Decorative geometric pattern of yellow triangles and diamonds"></div>

    <h2 class="abs define-head">What is a Gun Trust?</h2>
    <p class="abs define-body">A legally recognized trust that allows you to collect, own, and transfer firearms, including those restricted by the KRC.</p>
    <div class="photo light" style="left:13px;top:222px;width:178px;height:176px" role="img" aria-label="Illustration of a compass pointing to the word trust beside a handgun"></div>
    <p class="abs quote">“A gun trust is a revocable trust created to hold ownership of a firearm...” - BQM</p>

    <h2 class="abs section-head benefits-head">Benefits of a Gun Trust</h2>
    <div class="benefit" style="top:132px">
      <svg class="badge" viewBox="0 0 18 20" aria-hidden="true"><polygon points="9,1 17,5.5 17,14.5 9,19 1,14.5 1,5.5" fill="none" stroke="var(--yellow)" stroke-width="1.2"/><text x="9" y="13" text-anchor="middle" font-size="7" fill="var(--white)" font-family="Montserrat, sans-serif">01</text></svg>
      <h3>Avoid Probate:</h3>
      <p>Keep your firearms out of the public probate process.</p>
    </div>
    <div class="benefit" style="top:192px">
      <svg class="badge" viewBox="0 0 18 20" aria-hidden="true"><polygon points="9,1 17,5.5 17,14.5 9,19 1,14.5 1,5.5" fill="none" stroke="var(--yellow)" stroke-width="1.2"/><text x="9" y="13" text-anchor="middle" font-size="7" fill="var(--white)" font-family="Montserrat, sans-serif">02</text></svg>
      <h3>Multi-Generational Ownership:</h3>
      <p>Transfer ownership without court proceedings.</p>
    </div>
    <div class="benefit" style="top:267px">
      <svg class="badge" viewBox="0 0 18 20" aria-hidden="true"><polygon points="9,1 17,5.5 17,14.5 9,19 1,14.5 1,5.5" fill="none" stroke="var(--yellow)" stroke-width="1.2"/><text x="9" y="13" text-anchor="middle" font-size="7" fill="var(--white)" font-family="Montserrat, sans-serif">03</text></svg>
      <h3>Shared Responsibility:</h3>
      <p>Allow others to legally possess and use the firearms.</p>
    </div>

    <div class="photo wood" style="left:455px;top:105px;width:178px;height:182px" role="img" aria-label="Photo of a handgun in a foam-lined hard case on a wooden table"></div>
    <h2 class="abs section-head setup-head">How to Set Up a Gun Trust</h2>
    <ul class="abs setup-list">
      <li>Consult with an Attorney: A firearms trust attorney will create a trust.</li>
      <li>Assign a Trustee: Choose a trustee to manage the trust.</li>
      <li>Transfer Ownership: Assign your firearms to the trust.</li>
    </ul>
  </section>
</div>

</body>
</html>
```